Business Card Design Project

I have a two letter domain name zu.com.au (lower case font please). I want a business card, cum logo that is die cut (around the zu segment at least) that fits standard business card size.
zu is all about what 'I am' - a journalist, blogger, analyst, commentator. My mantra is "I think therefore zu'.
The reverse of the card only needs my name Olin Verka, email olin@zu.com.au and mobile +61 437 185 923
Mainly people that will use my professional writing services and suppliers that will provide product for review
Business
- One side is zu.com.au (hint - the .com.au can be vertical or horizontal to fit - the zu should be as large as possible).
The other requires large size font name, email and phone details (so no one needs glasses to read it).
The die cut can be just to highlight the zu segment - need not be around the whole card.
Font used in the past was Belwe (old style - very much like the i used in the information symbol).
Colours - no preference - prefer two colour to process colour but can also be an outline font instead of solid colour.

```html
<!DOCTYPE html>
<html lang="en">
<head>
<meta charset="utf-8">
<title>zu.com.au business card</title>
<link rel="stylesheet" href="https://fonts.googleapis.com/css2?family=Coustard:wght@900&family=Tinos&display=swap">
<style>
  :root {
    --card-red: #ec1c24;
    --ink-white: #ffffff;
    --page-bg: #efe9e1;
  }
  * { box-sizing: border-box; margin: 0; padding: 0; }
  html, body {
    width: 1200px;
    height: 960px;
    overflow: hidden;
    background: var(--page-bg);
  }
  .sheet {
    width: 1200px;
    height: 960px;
    display: flex;
    flex-direction: column;
    align-items: center;
    justify-content: center;
    gap: 60px;
  }
  .card {
    position: relative;
    width: 640px;
    height: 390px;
    background: var(--card-red);
    border-radius: 26px;
    box-shadow: 0 6px 18px rgba(0,0,0,0.18);
    color: var(--ink-white);
    overflow: hidden;
  }

  /* Front */
  .brand {
    position: absolute;
    left: 0; right: 0;
    top: 50%;
    transform: translateY(-50%);
    text-align: center;
    font-family: "Tinos", serif;
    font-weight: 400;
    font-size: 104px;
    line-height: 1;
    color: var(--ink-white);
  }
  .corner-name {
    position: absolute;
    left: 30px;
    bottom: 26px;
    font-family: "Tinos", serif;
    font-weight: 400;
    font-size: 22px;
    line-height: 1;
    color: var(--ink-white);
  }

  /* Back */
  .contact {
    position: absolute;
    left: 56px;
    top: 64px;
  }
  .contact-name {
    font-family: "Coustard", serif;
    font-weight: 900;
    font-size: 44px;
    letter-spacing: 2px;
    margin-bottom: 22px;
  }
  .contact-line {
    display: flex;
    align-items: center;
    gap: 22px;
    font-family: "Tinos", serif;
    font-size: 38px;
    letter-spacing: 2px;
    line-height: 1.3;
    margin-bottom: 6px;
  }
  .contact-line svg { flex: none; }
  .back-name {
    position: absolute;
    right: 30px;
    bottom: 24px;
    font-family: "Tinos", serif;
    font-weight: 400;
    font-size: 22px;
    line-height: 1;
    color: var(--ink-white);
  }
</style>
</head>
<body>
<main class="sheet">
  <section class="card card-front" aria-label="Card front">
    <h1 class="brand">zu.com.au</h1>
    <span class="corner-name">zu</span>
  </section>

  <section class="card card-back" aria-label="Card back">
    <div class="contact">
      <p class="contact-name">Olin Verka</p>
      <p class="contact-line">
        <svg width="24" height="18" viewBox="0 0 24 18" aria-hidden="true">
          <rect x="1" y="1" width="22" height="16" fill="none" stroke="#fff" stroke-width="2"/>
          <path d="M1 1 L12 10 L23 1" fill="none" stroke="#fff" stroke-width="2"/>
        </svg>
        <span>olin@zu.com.au</span>
      </p>
      <p class="contact-line">
        <svg width="24" height="26" viewBox="0 0 24 26" aria-hidden="true">
          <rect x="3" y="1" width="18" height="24" rx="3" fill="none" stroke="#fff" stroke-width="2"/>
          <line x1="3" y1="19" x2="21" y2="19" stroke="#fff" stroke-width="2"/>
        </svg>
        <span>+61 437 185 923</span>
      </p>
    </div>
    <span class="back-name">zu.com.au</span>
  </section>
</main>
</body>
</html>
```